BildeVOLD buisnesscard

Hey :) I need a modern buisnesscard for my company BildeVOLD
It most have:
Dagligleder og Fotograf: Henrik Audun Strandvik

Mob: +4791264085
Epost: post@bildevold.example
Adresse: Kvernbakken9, 6040 Langevåg

Facbook and instagram logo with text BildeVOLD

BildeVOLD logo

It Company

```html
<!DOCTYPE html>
<html lang="no">
<head>
<meta charset="utf-8">
<title>BildeVOLD – visittkort</title>
<link rel="stylesheet" href="https://fonts.googleapis.com/css2?family=Source+Sans+3:wght@400;600;700&display=swap">
<style>
  :root {
    --stage: #4a4a4a;
    --card: #ffffff;
    --blue: #2383b7;
    --pink: #cc4386;
    --pink-soft: #d9679f;
    --text: #4d4d4d;
    --white: #ffffff;
  }
  * { box-sizing: border-box; margin: 0; padding: 0; }
  html, body {
    width: 1105px; height: 1200px; overflow: hidden;
    background: var(--stage);
    font-family: "Source Sans 3", "Myriad Pro", sans-serif;
  }
  .card {
    position: absolute; left: 193px; width: 720px; height: 412px;
    box-shadow: 0 4px 10px rgba(0,0,0,.45);
    overflow: hidden;
  }
  .card--front { top: 167px; background: var(--card); }
  .card--back { top: 623px; background: var(--pink); }

  .brand-square {
    position: absolute; left: 41px; top: 48px;
    width: 72px; height: 72px; background: var(--pink);
  }
  .brand-name {
    position: absolute; left: 41px; top: 128px;
    font-size: 56px; line-height: 64px; font-weight: 700;
    color: var(--blue); letter-spacing: .5px;
  }
  .address {
    position: absolute; left: 41px; top: 226px;
    font-size: 19px; line-height: 26px; color: var(--text); font-style: normal;
  }
  .contact {
    position: absolute; left: 41px; top: 290px; list-style: none;
    font-size: 19px; line-height: 27px; color: var(--text);
  }
  .contact li { display: flex; align-items: center; gap: 10px; }
  .contact svg { width: 16px; height: 18px; fill: var(--blue); }

  .person {
    position: absolute; right: 43px; top: 256px; text-align: right;
  }
  .person__name { font-size: 26px; font-weight: 600; color: var(--blue); line-height: 32px; }
  .person__role { font-size: 20px; color: var(--pink); line-height: 30px; }

  .band {
    position: absolute; bottom: 0; height: 35px;
  }
  .band--web { left: 0; width: 605px; background: var(--blue); }
  .band--accent { left: 605px; right: 0; background: var(--pink); }
  .website {
    position: absolute; left: 50px; top: 4px;
    font-size: 19px; color: var(--white);
  }

  .back-brand {
    position: absolute; left: 0; right: 0; top: 146px; text-align: center;
    font-size: 66px; line-height: 76px; font-weight: 700;
    color: var(--white); letter-spacing: 1px;
  }
  .social {
    position: absolute; left: 0; right: 0; top: 232px;
    display: flex; justify-content: center; align-items: center; gap: 6px;
  }
  .social__rule { width: 93px; height: 1.5px; background: rgba(255,255,255,.75); margin: 0 4px; }
  .social__dot {
    width: 36px; height: 36px; border-radius: 50%;
    border: 2px solid var(--white);
    background: var(--pink-soft);
  }
</style>
</head>
<body>
  <section class="card card--front">
    <div class="brand-square"></div>
    <div class="brand-name">BildeVOLD</div>

    <address class="address">
      Kvernbakken9<br>6040 Langevåg
    </address>

    <ul class="contact">
      <li>
        <svg viewBox="0 0 16 18" aria-hidden="true"><path d="M4 0h8a2 2 0 0 1 2 2v14a2 2 0 0 1-2 2H4a2 2 0 0 1-2-2V2a2 2 0 0 1 2-2zm0 2.5v11h8v-11zM8 14.5a1 1 0 1 0 0 2 1 1 0 0 0 0-2z"/></svg>
        +4791264085
      </li>
      <li>
        <svg viewBox="0 0 16 18" aria-hidden="true"><path d="M0 5h16v10H0zm1.5 1.3V13.5h13V6.3L8 11z"/><path d="M0 5l8 6 8-6z"/></svg>
        post@bildevold.example
      </li>
    </ul>

    <div class="person">
      <div class="person__name">Henrik Audun Strandvik</div>
      <div class="person__role">Dagligleder og Fotograf</div>
    </div>

    <div class="band band--web"><span class="website">www.bildevold.example</span></div>
    <div class="band band--accent"></div>
  </section>

  <section class="card card--back">
    <div class="back-brand">BildeVOLD</div>
    <div class="social" role="img" aria-label="Sosiale medier">
      <span class="social__rule"></span>
      <span class="social__dot"></span>
      <span class="social__dot"></span>
      <span class="social__rule"></span>
    </div>
  </section>
</body>
</html>
```